Business Cards Needed for Innovative Healthcare Marketing Company

We are a marketing company focused on healthcare. Our company is all about rebranding yourself renewing your image and generating results. The phoenix stands for "reborn" or "rising" which we provide new brands for our clients we take their old brands and renew it with creativity and innovation. I am looking for a business card with color dimension. I have attached an example of a card I think has the look and feel of what I am trying to accomplish. I like that the card example has black and grey font colors, I like the font placement and the small logo, I really like the use of the colors on the right those are the colors of my logo. My logo is phoenix so maybe incorporating flames similar to that design. I would like the back a solid color maybe red with an opaque version of the logo and website. As a marketing company I am always open to creative liberty!

Target Market(s)

Doctors and business professionals.

Industry/Entity Type

Marketing

Contact Information for Business Card

Valcorne Health Care Marketing
Marla Tenwick- CEO
#(512)638-2974
email-marla@valcorne.com
website- valcorne.com

Font styles to use
Sans Serif

Colors
ec1f27
f37122
ffc214
fbed22
fbf289
f04a50

Requirements
Must have
• The logo and required information
Nice to have
• icons by the information
Should not have
• child like font

```html
<!DOCTYPE html>
<html lang="en">
<head>
<meta charset="utf-8">
<title>Valcorne Health Care Marketing – Business Card</title>
<link rel="stylesheet" href="https://fonts.googleapis.com/css2?family=Open+Sans:wght@300;400;700&display=swap">
<style>
  :root {
    --red: #ec1f27;
    --red-soft: #f04a50;
    --orange: #f37122;
    --gold: #ffc214;
    --yellow: #fbed22;
    --yellow-pale: #fbf289;
    --ink: #3a3a3a;
    --card: #ffffff;
    --stage: #e9e6e1;
  }
  * { box-sizing: border-box; margin: 0; padding: 0; }
  html, body { width: 1200px; height: 1023px; overflow: hidden; }
  body {
    background: var(--stage);
    font-family: "Open Sans", Arial, sans-serif;
    position: relative;
  }
  .card {
    position: absolute;
    width: 560px;
    height: 320px;
    background: linear-gradient(135deg, #ffffff 0%, #f4f4f4 100%);
    border-radius: 16px;
    overflow: hidden;
    box-shadow: 0 10px 28px rgba(0,0,0,0.18);
  }
  .card-front { left: 70px; top: 110px; }
  .card-back { left: 570px; top: 590px; }
  .card-shapes { position: absolute; inset: 0; width: 100%; height: 100%; }

  .brand { position: absolute; display: flex; align-items: center; gap: 12px; }
  .brand-dot { border-radius: 50%; background: var(--orange); flex: none; }
  .brand-name, .brand-sub { color: var(--red); font-weight: 300; line-height: 1.1; white-space: nowrap; }

  .card-front .brand { left: 34px; top: 34px; }
  .card-front .brand-dot { width: 46px; height: 46px; }
  .card-front .brand-name { font-size: 30px; letter-spacing: 1px; text-transform: uppercase; }
  .card-front .brand-sub { font-size: 9.5px; letter-spacing: 1px; text-transform: uppercase; border-top: 1px solid var(--red-soft); padding-top: 3px; margin-top: 3px; }

  .feature-mark {
    position: absolute; right: 60px; top: 26px;
    width: 150px; height: 150px; border-radius: 50%;
    background: var(--gold);
  }

  .person { position: absolute; left: 92px; top: 150px; }
  .person-name { color: var(--red); font-weight: 700; font-size: 24px; }
  .person-title { color: var(--orange); font-size: 13px; margin-top: -2px; }

  .contacts { position: absolute; left: 92px; top: 214px; list-style: none; }
  .contacts li { display: flex; align-items: center; gap: 10px; color: var(--ink); font-size: 13px; height: 26px; }
  .icon { width: 18px; height: 18px; flex: none; }

  .card-back .brand {
    left: 100px; right: 100px; top: 0; bottom: 0;
    justify-content: center; gap: 14px;
  }
  .card-back .brand-dot { width: 54px; height: 54px; }
  .card-back .brand-name { font-size: 40px; letter-spacing: 2px; text-transform: uppercase; }
  .card-back .brand-sub { font-size: 10.5px; letter-spacing: 1.5px; text-transform: uppercase; border-top: 1px solid var(--red-soft); padding-top: 4px; margin-top: 4px; }
</style>
</head>
<body>

<section class="card card-front" aria-label="Card front">
  <svg class="card-shapes" viewBox="0 0 560 320" aria-hidden="true">
    <polygon points="300,320 470,220 560,220 560,320" fill="var(--yellow)"/>
    <polygon points="420,250 560,150 560,190 470,250" fill="var(--orange)"/>
    <polygon points="500,190 560,60 560,150" fill="var(--gold)"/>
  </svg>
  <div class="feature-mark" aria-hidden="true"></div>
  <div class="brand">
    <span class="brand-dot" aria-hidden="true"></span>
    <div>
      <div class="brand-name">Valcorne</div>
      <div class="brand-sub">Health Care Marketing</div>
    </div>
  </div>
  <div class="person">
    <div class="person-name">Marla Tenwick</div>
    <div class="person-title">CEO</div>
  </div>
  <ul class="contacts">
    <li>
      <svg class="icon" viewBox="0 0 18 18" aria-hidden="true"><rect width="18" height="18" rx="3" fill="var(--gold)"/><path d="M5 4.5c1 0 1.5 2 1.5 2.5S5.8 8 6.3 9s1.7 2.3 2.7 2.7 1-.7 2-.7 2.5.5 2.5 1.5-1.5 2-2.5 2C7.5 14.5 3.5 10.5 3.5 7c0-1 .5-2.5 1.5-2.5z" fill="#fff"/></svg>
      (512)638-2974
    </li>
    <li>
      <svg class="icon" viewBox="0 0 18 18" aria-hidden="true"><rect width="18" height="18" rx="3" fill="var(--gold)"/><rect x="4" y="5.5" width="10" height="7" fill="none" stroke="#fff" stroke-width="1.3"/><path d="M4 5.5l5 4 5-4" fill="none" stroke="#fff" stroke-width="1.3"/></svg>
      marla@valcorne.com
    </li>
    <li>
      <svg class="icon" viewBox="0 0 18 18" aria-hidden="true"><circle cx="9" cy="9" r="7.5" fill="none" stroke="var(--gold)" stroke-width="1.4"/><ellipse cx="9" cy="9" rx="3.2" ry="7.5" fill="none" stroke="var(--gold)" stroke-width="1.2"/><path d="M1.5 9h15M3 5h12M3 13h12" stroke="var(--gold)" stroke-width="1.1"/></svg>
      www.valcorne.com
    </li>
  </ul>
</section>

<section class="card card-back" aria-label="Card back">
  <svg class="card-shapes" viewBox="0 0 560 320" aria-hidden="true">
    <polygon points="0,0 110,0 60,80 0,80" fill="var(--gold)"/>
    <polygon points="0,80 60,80 70,240 0,240" fill="var(--yellow)"/>
    <polygon points="60,80 78,80 88,240 70,240" fill="var(--orange)"/>
    <polygon points="0,240 70,240 130,320 0,320" fill="var(--gold)"/>
    <polygon points="450,0 560,0 560,80 500,80" fill="var(--gold)"/>
    <polygon points="500,80 560,80 560,240 490,240" fill="var(--yellow)"/>
    <polygon points="482,80 500,80 490,240 472,240" fill="var(--orange)"/>
    <polygon points="490,240 560,240 560,320 430,320" fill="var(--gold)"/>
  </svg>
  <div class="brand">
    <div>
      <div class="brand-name">Valcorne</div>
      <div class="brand-sub">Health Care Marketing</div>
    </div>
    <span class="brand-dot" aria-hidden="true"></span>
  </div>
</section>

</body>
</html>
```